Luxurious Product label and box for all natural skincare product. + 30AUD tip to winner.

What I require.
1.     One product label and one-box design.
2.     I must have a mock-up of the bottle with the attached label and the box.
 
I have supplied the following files for the designers to use.
1.     Brand logo file. (logo.zip)
2.     Slogan file. (slogan.psd)
3.     Slogan script file. (italianno.regular.ttf)
4.     Bottle image file. (60ml_moisturiser_bottle.png)
5.     Icon bar file. (Icon_bar_en.zip)
 
Label and box Design
I am interested in your unique design concepts and colors, so please feel free to be creative.
1.     Brand name: Velia
2.     You can use your own choice of colors in your design. I would prefer two colors (excluding logo and slogan colors), although more colors are acceptable for the right design.
3.     Label and box to have a background color or pattern.
4.     I would like the icon bar to wrap around the bottom of the label and box, covering the full width of all sides of the box.
5.     The height of the icon bar should be about 7mm to 10mm high.   
6.     The hex code for the icon bar color is #EDD6D4. The color of the icons can be any color the designer chooses.
7.     The positioning of the icons are as follows.
a)     The front panel has three icons. From left to right, they are; 100% Vegan, Product of Australia, and 100% Natural.
b)     The left side panel has three icons. From the front of the label/box to the back of the label/box, they are; Cruelty-Free, Ethical & Sustainable, and Please Recycle.
c)     The right side panel has only one icon situated at the front of the right side of the label/box. The icon is 6 Months Once Open.
 
Label.
1.     The label will be a three-panel label.
2.     The label will contain text in all three panels; however, only the text for the front panel of the label is supplied in this brief. For now, use Lorem Ipsum placeholder text to fill spaces.
3.     The final text will be provided to the winning designer so they can apply the text to the left and right panels of the label.
4.     Label size. Width 104mm x Height 83mm.
5.     The final design file must include bleed and cut lines.
 
Box.
1.     The box will contain text on all four sides; however, only the text for the front of the box is supplied in this brief. For now, use Lorem Ipsum placeholder text to fill spaces.
2.     The final text will be provided to the winning designer so they can apply the text to the left and right sides and the back of the box.
3.     The box size is 40mm wide x 40mm deep x 140mm high.
4.     The final design file must include bleed and cut lines.
 
Front Panel wording.
1.     Logo.
2.     Slogan.
3.     Moisturiser.
4.     Hydrate & Nourish.
5.     Hyaluronic Acid, Desert Lime & Green Tea.
6.     All Skin Types - Dry – Dehydrated.
7.     Icon bar.
8.     60mL
 
Bottle size
60ml White Bottle – 13.5cm High x 3.5cm Wide.

Target Market(s)

Beauty-minded Asian consumers between the age of 32 and 75 who take a proactive approach in maintaining younger-looking skin. Those who already know the danger of damaged skin caused by skincare containing harsh chemicals, and therefore choose effective natural/organic solutions to meet their skincare needs. Those who wish a more radiant glow and youthful appearance to their skin. Usually, a two-income middle to high-income bracket couple with a mindset for health and beauty.

Industry/Entity Type

Beauty and skincare.

Font styles to use
Other font styles liked:
• Logo and slogan script supplied. Designer to choose all other font or script.

Colors

Designer to choose colors to be used in the design.

Requirements
Must have
• A mock-up label on the bottle and a mock-up box. My logo and slogan are already designed with my chosen font and color.
Nice to have
• I like soft pastel colors with perhaps a small amount of stronger color.

```html
<!DOCTYPE html>
<html lang="en">
<head>
<meta charset="utf-8">
<title>Velia Moisturiser – Label and Box</title>
<link href="https://fonts.googleapis.com/css2?family=Barlow+Condensed:wght@300;400;600;700&family=Italianno&family=Open+Sans:wght@400;700&display=swap" rel="stylesheet">
<style>
:root{
  --stage:#7a7e8e;
  --blush:#ecd7d3;
  --cream:#eee2d6;
  --cocoa:#4b4543;
  --ink:#3f3a39;
  --paper:#ffffff;
  --muted:#6d6462;
}
*{box-sizing:border-box;margin:0;padding:0}
html,body{width:1200px;height:1117px;overflow:hidden;background:var(--stage)}
body{position:relative;font-family:"Barlow Condensed",sans-serif;color:var(--ink)}

.panel{position:absolute;background:linear-gradient(170deg,var(--blush) 0%,var(--blush) 45%,var(--cream) 100%);overflow:hidden}
.label-front{left:110px;top:300px;width:320px;height:600px}
.box-front{left:520px;top:140px;width:240px;height:840px}
.box-side{left:760px;top:140px;width:240px;height:840px;background:linear-gradient(175deg,#f3e9e4 0%,var(--cream) 100%);border-left:1px solid rgba(0,0,0,.08)}

.slogan-band{position:absolute;background:var(--cocoa);color:var(--paper);font-family:"Italianno",cursive;text-align:center}
.label-front .slogan-band{left:24px;right:24px;top:40px;height:90px;font-size:46px;line-height:90px}
.box-front .slogan-band{left:0;right:20px;top:22px;height:90px;font-size:40px;line-height:90px}

.brand{position:absolute;font-family:"Barlow Condensed",sans-serif;font-weight:400;color:var(--ink);letter-spacing:1px}
.label-front .brand{left:30px;top:150px;font-size:84px;line-height:1}
.box-front .brand{left:20px;top:220px;font-size:84px;line-height:1}

.product-name{position:absolute;font-weight:700;font-size:44px;line-height:1;color:var(--muted)}
.benefit{position:absolute;font-weight:600;font-size:28px;line-height:1.1;color:var(--muted)}
.label-front .product-name{left:30px;top:272px}
.label-front .benefit{left:30px;top:318px}
.box-front .product-name{left:20px;top:420px;font-size:40px}
.box-front .benefit{left:20px;top:466px;font-weight:400;font-size:34px;line-height:1.08}

.ingredients{position:absolute;background:var(--cocoa);color:var(--paper);border-radius:0 40px 0 0}
.label-front .ingredients{left:30px;top:360px;width:270px;height:70px;padding:8px 12px;font-size:22px;line-height:1.2;font-weight:400}
.box-front .ingredients{left:20px;top:560px;width:190px;height:108px;padding:6px 10px;font-size:26px;line-height:1.05;font-weight:300}

.skin-types{position:absolute;color:var(--muted)}
.label-front .skin-types{left:30px;top:440px;font-size:20px;font-weight:400}
.box-front .skin-types{left:20px;top:684px;font-size:25px;font-weight:300;line-height:1.15}

.icon-bar{position:absolute;left:0;right:0;background:var(--cocoa);display:flex;align-items:center;justify-content:space-around;color:var(--paper)}
.label-front .icon-bar{top:480px;height:62px}
.box-front .icon-bar,.box-side .icon-bar{top:752px;height:62px}
.badge{display:flex;flex-direction:column;align-items:center;font-family:"Open Sans",sans-serif;font-weight:700;font-size:7px;line-height:1.1;text-align:center}
.badge svg{width:26px;height:26px;margin-bottom:3px}

.volume{position:absolute;left:0;right:0;text-align:center;font-family:"Open Sans",sans-serif;font-size:15px;color:var(--ink)}
.label-front .volume{top:560px}
.box-front .volume{top:818px;font-size:13px}

.nutrition{position:absolute;left:20px;top:36px;width:165px;background:var(--paper);border:1px solid #222;padding:4px 5px;font-family:"Barlow Condensed",sans-serif;color:#111}
.nutrition h3{font-size:22px;font-weight:700;line-height:1;border-bottom:4px solid #111;padding-bottom:2px}
.nutrition .row{display:flex;justify-content:space-between;font-size:9px;line-height:1.3;border-bottom:1px solid #777}
.nutrition .row:last-child{border-bottom:none}
.nutrition .row.big{font-size:18px;font-weight:700;border-bottom:3px solid #111}
.nutrition .indent{padding-left:8px}

.side-copy{position:absolute;left:14px;width:175px;top:330px;font-family:"Open Sans",sans-serif;font-size:8.5px;line-height:1.35;text-align:center;color:var(--ink)}
.side-copy p{margin-bottom:22px}

.box-side .icon-bar{justify-content:flex-end;padding-right:10px}
</style>
</head>
<body>

<section class="panel label-front" aria-label="Bottle label front panel">
  <div class="slogan-band">grown by nature</div>
  <div class="brand">Velia</div>
  <div class="product-name">MOISTURISER</div>
  <div class="benefit">Hydrate &amp; Nourish</div>
  <div class="ingredients">Hyaluronic Acid<br>Desert Lime &amp; Green Tea.</div>
  <div class="skin-types">All Skin Types Dry – Dehydrated</div>
  <div class="icon-bar">
    <div class="badge"><svg viewBox="0 0 24 24" fill="none" stroke="#fff" stroke-width="1.6"><path d="M12 21s-8-5.5-8-11a4.5 4.5 0 0 1 8-2.8A4.5 4.5 0 0 1 20 10c0 5.5-8 11-8 11z"/></svg>100%<br>Vegan</div>
    <div class="badge"><svg viewBox="0 0 24 24" fill="none" stroke="#fff" stroke-width="1.6"><circle cx="12" cy="12" r="8"/></svg>Product of<br>Australia</div>
    <div class="badge"><svg viewBox="0 0 24 24" fill="none" stroke="#fff" stroke-width="1.6"><path d="M12 20c-4-2-5-7-3-11 2 2 3 6 3 11zM12 20c4-2 5-7 3-11-2 2-3 6-3 11zM12 20c-4 0-7-3-8-6 3-1 6 1 8 6zM12 20c4 0 7-3 8-6-3-1-6 1-8 6z"/></svg>100%<br>Natural</div>
  </div>
  <div class="volume">60mL</div>
</section>

<section class="panel box-front" aria-label="Box front panel">
  <div class="slogan-band">grown by nature</div>
  <div class="brand">Velia</div>
  <div class="product-name">MOISTURISER</div>
  <div class="benefit">Hydrate<br>&amp; Nourish</div>
  <div class="ingredients">Hyaluronic Acid<br>Desert Lime &amp;<br>Green Tea.</div>
  <div class="skin-types">All Skin Types<br>Dry – Dehydrated</div>
  <div class="icon-bar">
    <div class="badge"><svg viewBox="0 0 24 24" fill="none" stroke="#fff" stroke-width="1.6"><path d="M12 21s-8-5.5-8-11a4.5 4.5 0 0 1 8-2.8A4.5 4.5 0 0 1 20 10c0 5.5-8 11-8 11z"/></svg>100%<br>Vegan</div>
    <div class="badge"><svg viewBox="0 0 24 24" fill="none" stroke="#fff" stroke-width="1.6"><circle cx="12" cy="12" r="8"/></svg>Product of<br>Australia</div>
    <div class="badge"><svg viewBox="0 0 24 24" fill="none" stroke="#fff" stroke-width="1.6"><path d="M12 20c-4-2-5-7-3-11 2 2 3 6 3 11zM12 20c4-2 5-7 3-11-2 2-3 6-3 11zM12 20c-4 0-7-3-8-6 3-1 6 1 8 6zM12 20c4 0 7-3 8-6-3-1-6 1-8 6z"/></svg>100%<br>Natural</div>
  </div>
  <div class="volume">60mL</div>
</section>

<section class="panel box-side" aria-label="Box side panel">
  <div class="nutrition">
    <h3>Nutrition Facts</h3>
    <div class="row"><span>10 servings per container</span></div>
    <div class="row"><b>Serving size</b><b>1 cup (55g)</b></div>
    <div class="row big"><span>Calories</span><span>165</span></div>
    <div class="row"><span>Total Fat 1.5g</span><b>2%</b></div>
    <div class="row indent"><span>Saturated Fat 0.5g</span><b>3%</b></div>
    <div class="row indent"><span>Trans Fat 0g</span></div>
    <div class="row indent"><span>Polyunsaturated Fat 0.5g</span></div>
    <div class="row indent"><span>Monounsaturated Fat 0.5g</span></div>
    <div class="row"><span>Cholesterol 0mg</span><b>0%</b></div>
    <div class="row"><span>Sodium 180mg</span><b>8%</b></div>
    <div class="row"><span>Fluoride 0g</span></div>
    <div class="row"><span>Total Carbohydrate 21g</span><b>8%</b></div>
    <div class="row indent"><span>Dietary Fiber 2g</span><b>7%</b></div>
    <div class="row indent"><span>Soluble Fiber &lt;1g</span></div>
    <div class="row indent"><span>Insoluble Fiber 1g</span></div>
    <div class="row indent"><span>Total Sugars 8g</span></div>
  </div>
  <div class="side-copy">
    <p>Lorem ipsum dolor sit amet, consectetuer adipiscing elit, sed diam nonummy nibh euismod tincidunt ut laoreet dolore magna aliquam erat volutpat.</p>
    <p>Lorem ipsum dolor sit amet, consectetuer adipiscing elit, sed diam nonummy nibh euismod tincidunt ut laoreet dolore magna aliquam erat volutpat.</p>
    <p>Lorem ipsum dolor sit amet, consectetuer adipiscing elit, sed diam nonummy nibh euismod tincidunt ut laoreet dolore magna aliquam erat volutpat.</p>
    <p>Lorem ipsum dolor sit amet, consectetuer adipiscing elit, sed diam nonummy nibh euismod tincidunt ut laoreet dolore magna aliquam erat volutpat.</p>
  </div>
  <div class="icon-bar">
    <div class="badge"><svg viewBox="0 0 24 24" fill="none" stroke="#fff" stroke-width="1.6"><rect x="6" y="8" width="12" height="13" rx="1"/><path d="M7 5h10v3H7z"/><text x="12" y="17" fill="#fff" stroke="none" font-size="6" text-anchor="middle" font-family="sans-serif">6M</text></svg>6 Months<br>Once Open</div>
  </div>
</section>

</body>
</html>
```